Business card for law firm

Need business card for new law firm. Think confident, authoritative, conservative, but not stuffy or old-fashioned.

Contact Information for Business Card

Content for card - logo (uploaded), plus the following:

Paul Whitcombe (larger font)
Managing Partner (larger font, but not as large as name)
Level 9, 7 Ferris Lane
Sydney NSW 2000
Main Tel 02 9364 2710
Direct Tel 02 8472 3159
Email paul@qvlegal.com.au
www.qvlegal.com.au

Letterhead design should include logo plus:
Level 9, 7 Ferris Lane
Sydney NSW 2000
Tel 02 8472 3159
www.qvlegal.com.au

```html
<!DOCTYPE html>
<html lang="en">
<head>
<meta charset="utf-8">
<title>Quayview Legal – Business Card</title>
<link rel="stylesheet" href="https://fonts.googleapis.com/css2?family=EB+Garamond:wght@400;500&family=Roboto:wght@400&display=swap">
<style>
  :root{
    --navy:#021d57;
    --ink:#141414;
    --grey:#5a5a5a;
    --rule:#c9c9c9;
    --paper:#ffffff;
    --backdrop:#e4e4e4;
  }
  *{box-sizing:border-box;margin:0;padding:0}
  html,body{width:1125px;height:1200px;overflow:hidden;background:var(--backdrop)}
  .card{position:absolute;left:171px;width:826px;height:471px}
  .card--front{top:106px;background:var(--paper)}
  .card--back{top:639px;background:var(--navy)}

  .brand{position:absolute;left:40px;width:360px;top:130px;text-align:center}
  .brand__mark{display:block;width:56px;height:56px;margin:0 auto 30px;background:var(--navy)}
  .brand__name{font-family:"EB Garamond",serif;font-weight:400;font-size:40px;letter-spacing:3px;color:var(--ink);white-space:nowrap}

  .divider{position:absolute;left:447px;top:100px;width:1px;height:270px;background:linear-gradient(var(--paper),var(--rule) 20%,var(--rule) 80%,var(--paper))}

  .contact{position:absolute;left:485px;top:112px}
  .contact__name{font-family:"EB Garamond",serif;font-weight:400;font-size:33px;line-height:1;color:var(--navy);letter-spacing:.3px}
  .contact__role{font-family:"EB Garamond",serif;font-size:21px;line-height:1.1;color:var(--ink);letter-spacing:.4px}
  .contact__address{margin-top:18px;font-family:"Roboto",sans-serif;font-size:19px;line-height:27px;color:var(--grey)}
  .contact__list{list-style:none;margin-top:14px;font-family:"Roboto",sans-serif;font-size:19px;line-height:26px;color:var(--grey)}
  .contact__list li{display:flex;align-items:center;gap:12px}
  .contact__list svg{width:18px;height:18px;fill:var(--navy);flex:none}

  .back-brand{position:absolute;left:0;right:0;top:120px;text-align:center}
  .back-brand__mark{display:block;width:90px;height:90px;margin:0 auto 36px;background:var(--paper)}
  .back-brand__name{font-family:"EB Garamond",serif;font-size:48px;letter-spacing:4px;color:var(--paper)}
  .back-url{position:absolute;left:0;right:0;top:405px;text-align:center;font-family:"Roboto",sans-serif;font-size:19px;letter-spacing:7px;color:var(--paper)}
</style>
</head>
<body>
  <section class="card card--front">
    <div class="brand">
      <span class="brand__mark"></span>
      <div class="brand__name">QUAYVIEW LEGAL</div>
    </div>
    <div class="divider"></div>
    <div class="contact">
      <h1 class="contact__name">PAUL WHITCOMBE</h1>
      <p class="contact__role">MANAGING PARTNER</p>
      <p class="contact__address">Level 9, 7 Ferris Lane<br>Sydney NSW 2000</p>
      <ul class="contact__list">
        <li><svg viewBox="0 0 24 24" aria-hidden="true"><path d="M6.6 10.8a15.1 15.1 0 0 0 6.6 6.6l2.2-2.2c.3-.3.7-.4 1-.2 1.1.4 2.3.6 3.6.6.6 0 1 .4 1 1V20c0 .6-.4 1-1 1A17 17 0 0 1 3 4c0-.6.4-1 1-1h3.5c.6 0 1 .4 1 1 0 1.3.2 2.5.6 3.6.1.3 0 .7-.2 1z"/></svg>02 9364 2710</li>
        <li><svg viewBox="0 0 24 24" aria-hidden="true"><path d="M6.6 10.8a15.1 15.1 0 0 0 6.6 6.6l2.2-2.2c.3-.3.7-.4 1-.2 1.1.4 2.3.6 3.6.6.6 0 1 .4 1 1V20c0 .6-.4 1-1 1A17 17 0 0 1 3 4c0-.6.4-1 1-1h3.5c.6 0 1 .4 1 1 0 1.3.2 2.5.6 3.6.1.3 0 .7-.2 1z"/></svg>02 8472 3159</li>
        <li><svg viewBox="0 0 24 24" aria-hidden="true"><path d="M2 5h20v14H2zm2 2v.4l8 5 8-5V7zm0 2.8V17h16V9.8l-8 5z"/></svg>paul@qvlegal.com.au</li>
        <li><svg viewBox="0 0 24 24" aria-hidden="true"><circle cx="12" cy="12" r="10"/></svg>www.qvlegal.com.au</li>
      </ul>
    </div>
  </section>

  <section class="card card--back">
    <div class="back-brand">
      <span class="back-brand__mark"></span>
      <div class="back-brand__name">QUAYVIEW LEGAL</div>
    </div>
    <p class="back-url">www.qvlegal.com.au</p>
  </section>
</body>
</html>
```